4D Cradle Glimpse Luxury Ultrasound Billboard

Design a HIGH-END, MODERN billboard for my private prenatal ultrasound studio, 4D Cradle Glimpse, located in Pace, Florida.
This billboard will be viewed by drivers traveling at highway speeds, so it must be extremely clean, simple, and readable within 6 seconds.
About My Business
4D Cradle Glimpse is a private prenatal ultrasound studio specializing in:
Highest technology 4D/HD Ultrasounds
Early Gender Determination
Pregnancy Confirmation
I have been serving families for nearly 10 years and is known for creating a memorable experience, not just an ultrasound appointment.
Design Style
I DO NOT want:
Flowers
Leaves
Swirls
Glitter
Hearts everywhere
Busy backgrounds
Generic maternity stock graphics
I DO want:
Modern
Luxury
Upscale
Clean
Professional
Eye-catching
Premium medical spa feel
Colors
Use colors from my logo:
LOGO Green ( or a deep green)
Black
White
Soft Gold accents
Images:
Incorporate my professional headshot in a clean, modern way, logo, and the ultrasound images
Text
Keep wording minimal.
Primary Headline ( OPEN TO IDEAS) :
EXAMPLES ( WOULD RATHER SOMETHING MORE CATCHY)
" ADVANCED IMAGING. UNFORGETTABLE MOMENTS"
"MEET YOUR BABY BEFORE BIRTH"
Under headline:
4D Ultrasound • Early Gender • Pregnancy Confirmation
Business Name:
4D Cradle Glimpse
Private Prenatal Ultrasound Studio
Phone Number:
850-471-5923
Important
This billboard must be readable in 5–6 seconds from a moving vehicle.
Less text is better.
The phone number and business name must be visible from a distance.
The design should feel like a premium brand that immediately tells expecting parents:
“This is where I go to see my baby.”
Files Provided
Official logo
Headshot
Ultrasound images
Don’t make this look like a medical office billboard.
Make it look like a luxury baby experience billboard. That’s what separates 4D Cradle Glimpse from hospitals, OB offices, and all the new studios popping up around you. The emotional connection is what gets moms to book. ❤️
Billboard Size - 10.6” x 36”

```html
<!DOCTYPE html>
<html lang="en">
<head>
<meta charset="utf-8">
<title>4D Cradle Glimpse Billboard</title>
<link href="https://fonts.googleapis.com/css2?family=Montserrat:wght@400;600;700&family=Open+Sans:wght@600;700&display=swap" rel="stylesheet">
<style>
  :root {
    --ink: #262e2b;
    --gold: #d2ad3f;
    --white: #ffffff;
    --sage: #7d8f88;
    --page: #eceeed;
  }
  * { margin: 0; padding: 0; box-sizing: border-box; }
  html, body { width: 1200px; height: 800px; overflow: hidden; background: var(--page); }
  .billboard {
    position: absolute; left: 40px; top: 235px;
    width: 1120px; height: 330px;
    background: var(--ink);
    overflow: hidden;
    font-family: "Montserrat", sans-serif;
    color: var(--white);
  }
  .headline {
    position: absolute; left: 36px; top: 30px;
    font-weight: 400; font-size: 54px; line-height: 1.08;
    letter-spacing: -0.5px; text-transform: uppercase;
  }
  .headline .accent { color: var(--gold); font-weight: 700; }
  .scan-photo {
    position: absolute; left: 30px; bottom: 24px;
    width: 78px; height: 108px; border-radius: 16px;
    border: 2px solid var(--white);
    background: radial-gradient(circle at 45% 45%, #c98a73, #8a4a3a 65%, #5a2c22);
  }
  .services {
    position: absolute; left: 130px; bottom: 34px;
    list-style: none;
    font-family: "Open Sans", sans-serif; font-weight: 600; font-size: 18px; line-height: 1.45;
  }
  .services li::before {
    content: ""; display: inline-block; width: 5px; height: 5px; border-radius: 50%;
    background: var(--gold); margin-right: 8px; vertical-align: middle;
  }
  .brand {
    position: absolute; left: 540px; top: 92px; width: 300px; text-align: center;
  }
  .brand-name {
    font-weight: 700; font-size: 34px; line-height: 1.1; color: var(--gold);
  }
  .brand-rule { display: block; margin: 12px auto 10px; width: 260px; height: 1px; background: var(--gold); }
  .brand-tagline { font-weight: 600; font-size: 13px; letter-spacing: 0.8px; text-transform: uppercase; }
  .phone {
    position: absolute; left: 540px; bottom: 46px; width: 300px; text-align: center;
    font-family: "Open Sans", sans-serif; font-weight: 700; font-size: 38px; letter-spacing: 0.5px;
  }
  .headshot {
    position: absolute; right: 0; top: 0; width: 270px; height: 100%;
    background: linear-gradient(160deg, #9aa3a1 0%, #d9c39a 30%, #3e5a47 70%, #2f3a35 100%);
  }
</style>
</head>
<body>
  <section class="billboard">
    <h1 class="headline">Meet your<br><span class="accent">Baby</span> before<br>birth</h1>

    <div class="scan-photo" role="img" aria-label="4D ultrasound image of twin babies"></div>
    <ul class="services">
      <li>4D Ultrasound</li>
      <li>Early Gender</li>
      <li>Pregnancy Confirmation</li>
    </ul>

    <div class="brand">
      <p class="brand-name">4D Cradle Glimpse</p>
      <span class="brand-rule"></span>
      <p class="brand-tagline">Prenatal Ultrasound Studio</p>
    </div>

    <p class="phone">850-471-5923</p>

    <div class="headshot" role="img" aria-label="Professional headshot of the sonographer in green scrubs holding an ultrasound probe beside the scanning machine"></div>
  </section>
</body>
</html>
```